Founder / concept developer needs business card // Consultant needs VCARD

I need a business card for me as a founding consultant in Berlin. I advise entrepreneurs, especially in the design of business ideas, business plans or financing applications. More information about this in the annexes. My USP: I design / structure complex ideas and projects convincingly so that my client is successful. I want to communicate professionalism, effectiveness and clarity. Colors like from the range BLACK-GRAY-GREEN. I am 27 years old, I have studied business for 7 years. Attachments: - Business card design (only idea, do not focus on it) - Website screenshot (only idea, do not focus on it)

Target Market(s)

Target group: Founder (20-50 yrs, m / w, needy, in "break-up phase") and CONTRACTOR / "financier" (30-55 yrs, m / w, often public service "routine-oriented"). The foundations are in quite different industries: digital, craft, tourism, retail, services, etc. Almost all German.

Industry/Entity Type

Consultant

Contact Information for Business Card

Lukas Brennwald
M. Sc., International Business Administration
Gründungsberater, Konzeptentwickler
www.kelvoran-mitrel.de
Postfach-Zugang@kelvoran.de
Tel. 0481 294 3172

Colors

Designer to choose colors to be used in the design.

Requirements
Must have
• Professionalism, persuasiveness, clarity
Nice to have
• memorability
Should not have
• Schnörkelei

```html
<!DOCTYPE html>
<html lang="de">
<head>
<meta charset="utf-8">
<title>Lukas Brennwald – Visitenkarte</title>
<link href="https://fonts.googleapis.com/css2?family=Work+Sans:wght@400;500;600&display=swap" rel="stylesheet">
<style>
  :root {
    --backdrop: #2b2b2b;
    --brand-green: #3eaa4a;
    --brand-green-dark: #1f7a32;
    --brand-green-light: #9ed3a6;
    --card-white: #ffffff;
    --text-gray: #5a5a5a;
    --text-dark: #333333;
  }
  * { box-sizing: border-box; margin: 0; padding: 0; }
  html, body { width: 1200px; height: 930px; overflow: hidden; }
  body {
    background: var(--backdrop);
    font-family: "Work Sans", Arial, sans-serif;
    position: relative;
  }
  .card {
    position: absolute;
    width: 560px;
    height: 340px;
    border-radius: 26px;
    overflow: hidden;
  }
  /* back side */
  .card-back {
    left: 90px;
    top: 110px;
    background: var(--brand-green);
  }
  .card-back .mark-area {
    position: absolute;
    left: 205px;
    top: 70px;
    width: 150px;
    height: 140px;
    border-radius: 14px;
    background: linear-gradient(150deg, var(--brand-green-dark), #2f8f3f 55%, var(--brand-green-light));
  }
  .card-back .web {
    position: absolute;
    left: 0; right: 0;
    bottom: 40px;
    text-align: center;
    color: var(--card-white);
    font-size: 15px;
    letter-spacing: 0.3px;
  }
  /* front side */
  .card-front {
    left: 570px;
    top: 470px;
    background: var(--card-white);
  }
  .card-front .accent-tab {
    position: absolute;
    left: 0;
    top: 160px;
    width: 34px;
    height: 180px;
    background: var(--brand-green);
    border-radius: 0 34px 0 0;
  }
  .card-front .mark-area {
    position: absolute;
    right: 40px;
    top: 34px;
    width: 160px;
    height: 150px;
    border-radius: 16px;
    background: linear-gradient(150deg, var(--brand-green-dark), var(--brand-green) 50%, var(--brand-green-light));
  }
  .identity {
    position: absolute;
    left: 62px;
    top: 146px;
    width: 290px;
  }
  .identity .name {
    color: var(--brand-green);
    font-size: 28px;
    font-weight: 500;
    letter-spacing: 0.4px;
    line-height: 34px;
    margin-bottom: 4px;
    white-space: nowrap;
  }
  .identity .degree,
  .identity .role {
    color: var(--text-gray);
    font-size: 14px;
    line-height: 17px;
    white-space: nowrap;
  }
  .identity .role { margin-top: 8px; }
  .contacts {
    list-style: none;
    margin-top: 10px;
  }
  .contacts li {
    display: flex;
    align-items: center;
    gap: 10px;
    color: var(--text-dark);
    font-size: 15px;
    line-height: 20px;
    white-space: nowrap;
  }
  .contacts svg { width: 12px; height: 12px; flex: none; fill: none; stroke: var(--brand-green); stroke-width: 1.6; }
  .contacts .highlight { color: var(--brand-green); }
</style>
</head>
<body>
  <section class="card card-back" aria-label="Rückseite der Visitenkarte">
    <div class="mark-area" role="img" aria-label="Fläche für die Bildmarke"></div>
    <p class="web">www.kelvoran-mitrel.de</p>
  </section>

  <section class="card card-front" aria-label="Vorderseite der Visitenkarte">
    <div class="accent-tab"></div>
    <div class="mark-area" role="img" aria-label="Fläche für die Bildmarke"></div>
    <div class="identity">
      <h1 class="name">Lukas Brennwald</h1>
      <p class="degree">M. Sc.,<br>International Business Administration</p>
      <p class="role">Gründungsberater,<br>Konzeptentwickler</p>
      <ul class="contacts">
        <li><svg viewBox="0 0 12 12"><path d="M2 1.5 L4 1.5 L5 4 L3.8 5 Q5 7.5 7 8.2 L8 7 L10.5 8 L10.5 10 Q6 11 2 5.5 Z"/></svg>0481 294 3172</li>
        <li><svg viewBox="0 0 12 12"><rect x="1" y="2.5" width="10" height="7" rx="1"/><path d="M1.5 3 L6 6.5 L10.5 3"/></svg>Postfach-Zugang@kelvoran.de</li>
        <li><svg viewBox="0 0 12 12"><circle cx="6" cy="6" r="5"/><path d="M1 6 H11 M6 1 Q3 6 6 11 Q9 6 6 1"/></svg><span>www.<span class="highlight">kelvoran-mitrel</span>.de</span></li>
      </ul>
    </div>
  </section>
</body>
</html>
```